Brookvane Consulting Business Card Design

Business Card Design for Brookvane Consulting. Brookvane Consulting is a boutique consultancy based in Atlanta, GA., that specializes in marketing strategy, organization planning, and leadership development. We provide solutions for small businesses and startups as well as Vantage 300 companies.

http://brookvaneconsulting.com/

Target Market(s)

We provide solutions for small businesses and startups as well as Vantage 300 companies.

Industry/Entity Type

Consulting

Contact Information for Business Card

Two sided business card with priority on contact information, logo, tag line (Guidance to Plan Boldly, Act Boldly, Lead Boldly)

Colors

Designer to choose colors to be used in the design.

Requirements
Must have
• contact information, logo, tag line (Guidance to Plan Boldly, Act Boldly, Lead Boldly)
• Simple no over communication.
Nice to have
• I would like to see different placements of logo and creative use of both sides of the card
Should not have
• Do not put too much information on the card.

```html
<!DOCTYPE html>
<html lang="en">
<head>
<meta charset="utf-8">
<title>Brookvane Consulting Business Card</title>
<link href="https://fonts.googleapis.com/css2?family=Lato:wght@300;400;700&display=swap" rel="stylesheet">
<style>
  :root {
    --backdrop: #3a332f;
    --card: #111213;
    --card-edge: #1a1b1d;
    --ink-strong: #f2f2f2;
    --ink-soft: #c9c9c9;
    --ink-muted: #9a9a9a;
    --rule: #5c5c5c;
  }
  html, body {
    margin: 0;
    padding: 0;
    width: 1200px;
    height: 769px;
    overflow: hidden;
    background: var(--backdrop);
    font-family: "Lato", sans-serif;
  }
  .canvas {
    position: relative;
    width: 1200px;
    height: 769px;
  }
  .card {
    position: absolute;
    top: 236px;
    width: 520px;
    height: 297px;
    background: var(--card);
    border: 1px solid var(--card-edge);
    box-sizing: border-box;
    box-shadow: 0 10px 30px rgba(0,0,0,0.45);
  }
  .card--back { left: 60px; }
  .card--front { left: 620px; }

  .contact {
    position: absolute;
    left: 30px;
    right: 30px;
    bottom: 34px;
  }
  .contact__headline {
    display: flex;
    align-items: baseline;
    gap: 12px;
    padding-left: 44px;
    padding-bottom: 7px;
    border-bottom: 1px solid var(--rule);
  }
  .contact__name {
    font-size: 16px;
    font-weight: 700;
    letter-spacing: 0.5px;
    color: var(--ink-muted);
    text-transform: uppercase;
  }
  .contact__sep { font-size: 14px; color: var(--ink-muted); }
  .contact__role { font-size: 14px; color: var(--ink-soft); }
  .contact__details {
    margin-top: 8px;
    font-size: 13px;
    color: var(--ink-soft);
    letter-spacing: 0.2px;
    white-space: nowrap;
  }

  .brand {
    position: absolute;
    left: 0;
    right: 0;
    top: 92px;
    text-align: center;
  }
  .brand__mark {
    display: inline-flex;
    align-items: center;
    gap: 12px;
  }
  .brand__square {
    width: 18px;
    height: 18px;
    border: 2px solid var(--ink-strong);
    box-sizing: border-box;
  }
  .brand__name {
    font-size: 34px;
    font-weight: 400;
    color: var(--ink-strong);
    letter-spacing: 0.5px;
  }
  .brand__tagline {
    margin: 38px 0 0;
    font-size: 12px;
    color: var(--ink-soft);
    letter-spacing: 0.3px;
  }
</style>
</head>
<body>
<main class="canvas">
  <section class="card card--back" aria-label="Card back with contact details">
    <div class="contact">
      <div class="contact__headline">
        <span class="contact__name">Darius Whitfield</span>
        <span class="contact__sep">-</span>
        <span class="contact__role">Founder/Managing Director</span>
      </div>
      <div class="contact__details">555-210-4837 | darius@brookvaneconsulting.com | brookvaneconsulting.com</div>
    </div>
  </section>

  <section class="card card--front" aria-label="Card front with brand name and tagline">
    <div class="brand">
      <div class="brand__mark">
        <span class="brand__square"></span>
        <span class="brand__name">Brookvane Consulting</span>
      </div>
      <p class="brand__tagline">Guidance to Plan Boldly, Act Boldly, Lead Boldly</p>
    </div>
  </section>
</main>
</body>
</html>
```